Website for Dental Office - The Bright Arch Clinic

The bright arch clinic is a dental office offering cosmetic dentistry, general dentistry, and multi-specialty dental care all under one roof in our state-of-the-art cosmetic dental center. We are particularly striving to provide services that fit the need of the young generation. Thus, we hope to have a modern, professional concise website that represents our spirit.

*Should be able to switch from English to Chinese

6 sections besides homepage:
Home, Meet us, Services,
Patient Info, Cases&Reviews, Blog, Contact

The Services sections should contain multiple subsections such as cleaning and prevention, cosmetic dentistry, implant dentistry, removable dentures, etc...
The Patient Info section is also intended to contain several subsections such as
New Patient offer, accepted Insurance, patient portal, helpful tips, etc...

Target Market(s)

young generation

Coding

Coded - Design and coding required

Number of Pages Required

5+ page

Font styles to use
Sans Serif

Colors
0592cd
33a6d7
85cae6
00a990
33b8a4
86cfc6
cee9f5
cfeae6
3277b5

Requirements
Must have
• *Should be able to switch from English to Chinese
Nice to have
• http://www.thebrightarchclinic.com/
• As a reference, the above link is the current website, but we would like to change the appearance and the content (our new logo's picture is attached)

```html
<!DOCTYPE html>
<html lang="en">
<head>
<meta charset="utf-8">
<title>Contact – The Bright Arch Clinic</title>
<link rel="stylesheet" href="https://fonts.googleapis.com/css2?family=Montserrat:wght@400;500;600;700;800&display=swap">
<style>
:root{
  --blue-deep:#0592cd;
  --blue:#33a6d7;
  --blue-soft:#85cae6;
  --teal:#00a990;
  --teal-mid:#33b8a4;
  --teal-soft:#86cfc6;
  --sky:#cee9f5;
  --mint:#cfeae6;
  --navy:#3277b5;
  --ink:#111;
  --text:#444;
  --muted:#666;
  --sea:#cdebf2;
  --grey:#f1f1f1;
  --grey-bar:#e9e9e9;
  --yellow:#fcc900;
}
*{box-sizing:border-box;margin:0;padding:0}
html,body{width:841px;height:1200px;overflow:hidden}
body{position:relative;background:#fff;font-family:"Montserrat",sans-serif;color:var(--text)}
.abs{position:absolute}
.topline{left:0;top:0;width:841px;height:2px;background:var(--navy)}
.hero-bg{left:0;top:0;width:841px;height:490px;background:linear-gradient(180deg,#d6effb 0%,#e6f5fc 45%,#fff 100%)}
.hero-cap{left:0;top:0}
/* header */
.brand{left:113px;top:13px;display:flex;align-items:center;gap:6px;font-size:12.5px;font-weight:700;color:var(--blue);line-height:1.15;width:160px}
.brand-sq{width:28px;height:28px;background:var(--blue-soft);border-radius:3px;flex:none}
.nav{left:279px;top:28px;width:318px;display:flex;justify-content:space-between;font-size:7px;font-weight:500;color:#444;white-space:nowrap}
.nav .on{color:var(--teal)}
.call{left:606px;top:-10px;width:79px;height:78px;border-radius:50%;background:var(--navy);color:#fff;text-align:center;font-weight:700;font-size:9px;padding-top:19px}
.call svg{display:block;margin:0 auto 5px}
.lang{left:693px;top:20px;width:35px;height:21px;background:var(--teal);border-radius:2px;color:#fff;font-size:7px;display:flex;align-items:center;justify-content:center;gap:3px}
h1.page-title{left:0;width:841px;top:150px;text-align:center;font-size:30px;font-weight:800;color:var(--ink);letter-spacing:.5px}
.h3{font-size:9.5px;font-weight:700;color:#222;letter-spacing:.3px}
.line{font-size:7.3px;color:var(--text);line-height:13px;letter-spacing:.2px}
.ico{position:absolute}
.map{left:438px;top:210px;width:290px;height:240px;background:linear-gradient(135deg,#ececec,#e3e3e3 60%,#dfe9f0)}
/* get in touch */
.sea{left:0;top:580px;width:841px;height:365px;background:var(--sea)}
h2.touch{left:0;width:841px;top:640px;text-align:center;font-size:29.5px;font-weight:800;color:var(--ink);letter-spacing:.3px}
.field{background:#fff;border-radius:2px;font-size:7.3px;color:#555;padding:9px 6px}
.send{left:357px;top:808px;width:127px;height:32px;border-radius:16px;background:var(--yellow);color:#111;font-weight:700;font-size:9px;display:flex;align-items:center;justify-content:center;letter-spacing:.3px}
/* footer */
.grey{left:0;top:943px;width:841px;height:225px;background:var(--grey)}
.cta{left:113px;top:886px;width:615px;height:115px;background:linear-gradient(90deg,var(--blue-deep),var(--teal));clip-path:polygon(0 0,100% 27%,100% 100%,0 100%);border-radius:5px}
.cta-small{left:128px;top:924px;font-size:8px;color:#fff}
.cta-big{left:128px;top:938px;font-size:25px;font-weight:800;color:#fff;letter-spacing:.3px}
.book{left:549px;top:941px;width:157px;height:31px;border-radius:16px;background:#fff;color:#222;font-weight:700;font-size:8.5px;display:flex;align-items:center;justify-content:center;letter-spacing:.3px}
.f-sq{left:149px;top:1036px;width:68px;height:46px;background:var(--blue-soft);border-radius:4px}
.f-brand{left:103px;top:1091px;width:160px;text-align:center;font-size:12px;font-weight:700;color:var(--blue);white-space:nowrap}
.soc{top:1114px;width:24px;height:24px;border-radius:50%}
.list{font-size:7.3px;color:var(--text);line-height:13.1px;letter-spacing:.2px}
.hours td{padding:0;height:13.1px;font-size:7.3px;color:var(--text)}
.hours td.t{font-weight:700;padding-left:6px;color:#333}
.bar{left:0;top:1168px;width:841px;height:32px;background:var(--grey-bar)}
.copy{left:114px;top:1178px;font-size:7.6px;color:#888}
.copy span{color:var(--navy)}
.credit{right:114px;top:1178px;font-size:7.6px;color:var(--teal)}
</style>
</head>
<body>
<div class="abs hero-bg"></div>
<svg class="abs hero-cap" width="841" height="110" viewBox="0 0 841 110"><path d="M0 0H841V47Q420 160 0 47Z" fill="#fff"/></svg>
<div class="abs topline"></div>

<header>
  <div class="abs brand"><span class="brand-sq"></span><span>The Bright Arch Clinic</span></div>
  <nav class="abs nav"><span>HOME</span><span>MEET US</span><span>SERVICES</span><span>PATIENT INFO</span><span>REVIEWS</span><span>BLOG</span><span class="on">CONTACT</span></nav>
  <div class="abs call"><svg width="16" height="16" viewBox="0 0 24 24"><path fill="#fff" d="M6.6 10.8a15 15 0 0 0 6.6 6.6l2.2-2.2a1 1 0 0 1 1-.25 11.4 11.4 0 0 0 3.6.57 1 1 0 0 1 1 1V20a1 1 0 0 1-1 1A17 17 0 0 1 3 4a1 1 0 0 1 1-1h3.5a1 1 0 0 1 1 1c0 1.25.2 2.45.57 3.57a1 1 0 0 1-.25 1Z"/></svg>555.214.7080</div>
  <div class="abs lang">汉语 <svg width="7" height="5" viewBox="0 0 10 6"><path d="M1 1l4 4 4-4" stroke="#fff" stroke-width="1.6" fill="none"/></svg></div>
</header>

<h1 class="abs page-title">CONTACT</h1>

<section>
  <div class="abs h3" style="left:115px;top:208px">CONTACT INFO</div>
  <svg class="ico" style="left:115px;top:235px" width="9" height="12" viewBox="0 0 12 16"><path d="M6 0a6 6 0 0 0-6 6c0 4.5 6 10 6 10s6-5.5 6-10a6 6 0 0 0-6-6Zm0 8.5A2.5 2.5 0 1 1 6 3.5a2.5 2.5 0 0 1 0 5Z" fill="var(--teal)"/></svg>
  <div class="abs line" style="left:130px;top:232px">2750 Harbor Lane, Suite 210,<br>Eastfield MA 02190</div>
  <svg class="ico" style="left:113px;top:268px" width="10" height="10" viewBox="0 0 24 24"><path fill="var(--navy)" d="M6.6 10.8a15 15 0 0 0 6.6 6.6l2.2-2.2a1 1 0 0 1 1-.25 11.4 11.4 0 0 0 3.6.57 1 1 0 0 1 1 1V20a1 1 0 0 1-1 1A17 17 0 0 1 3 4a1 1 0 0 1 1-1h3.5a1 1 0 0 1 1 1c0 1.25.2 2.45.57 3.57a1 1 0 0 1-.25 1Z"/></svg>
  <div class="abs" style="left:130px;top:267px;font-size:10px;font-weight:500;color:#444">555.214.7080</div>
  <svg class="ico" style="left:113px;top:294px" width="11" height="8" viewBox="0 0 22 16"><rect width="22" height="16" rx="2" fill="var(--blue)"/><path d="M1 2l10 7 10-7" stroke="#fff" stroke-width="1.6" fill="none"/></svg>
  <div class="abs line" style="left:130px;top:291px">info@thebrightarchclinic.com</div>

  <div class="abs h3" style="left:115px;top:334px">PUBLIC TRANSPORT</div>
  <div class="abs line" style="left:114px;top:356px;width:320px">2750 Harbor Lane, Suite 210, Harbor Line to Maple Ave.<br>Station (our office is located directly across from the stop). MA 02190</div>

  <div class="abs h3" style="left:115px;top:408px">PARKING</div>
  <svg class="ico" style="left:113px;top:433px" width="10" height="11" viewBox="0 0 20 22"><path d="M2 1h8a6 6 0 0 1 0 12H6v8H2ZM6 5v4h4a2 2 0 0 0 0-4Z" fill="none" stroke="var(--blue)" stroke-width="1.6"/></svg>
  <div class="abs line" style="left:130px;top:432px">Plenty of street and metered parking available.</div>

  <div class="abs map" role="img" aria-label="Street map showing the clinic location"></div>
</section>

<div class="abs sea"></div>
<svg class="abs" style="left:0;top:495px" width="841" height="100" viewBox="0 0 841 100">
  <path d="M0 7Q80 0 200 45Q300 85 420 82L480 80Q300 130 0 60Z" fill="#7fd0e1"/>
  <path d="M0 62Q120 90 236 88Q380 80 505 47Q600 27 683 28Q780 30 841 46V100H0Z" fill="var(--sea)"/>
  <path d="M0 28Q120 -5 250 20Q350 45 400 78L360 88Q200 70 0 40Z" fill="#bfe6ef" opacity=".7"/>
</svg>

<section>
  <h2 class="abs touch">GET IN TOUCH WITH US</h2>
  <div class="abs field" style="left:239px;top:695px;width:179px;height:23px">Name *</div>
  <div class="abs field" style="left:423px;top:695px;width:179px;height:23px">Contact No.</div>
  <div class="abs field" style="left:239px;top:724px;width:363px;height:23px">Email</div>
  <div class="abs field" style="left:239px;top:753px;width:363px;height:50px">Message</div>
  <div class="abs send">SEND MESSAGE</div>
</section>

<div class="abs grey"></div>
<div class="abs cta"></div>
<div class="abs cta-small">Lorem Ipsum is dummy text of the printing and typesetting.</div>
<div class="abs cta-big">YOUR SMILE. OUR PASSION.</div>
<div class="abs book">BOOK AN APPOINTMENT</div>

<footer>
  <div class="abs f-sq"></div>
  <div class="abs f-brand">The Bright Arch Clinic</div>
  <div class="abs soc" style="left:126px;background:var(--blue)"></div>
  <div class="abs soc" style="left:155px;background:var(--navy)"></div>
  <div class="abs soc" style="left:185px;background:var(--teal)"></div>
  <div class="abs soc" style="left:213px;background:var(--teal-mid)"></div>

  <div class="abs h3" style="left:274px;top:1031px;font-size:8.5px">USEFUL LINKS</div>
  <div class="abs list" style="left:273px;top:1050px">Home<br>Meet Us<br>Services<br>Patient Info<br>Case &amp; Reviews<br>Blog<br>Contact</div>

  <div class="abs h3" style="left:433px;top:1031px;font-size:8.5px">OPENING HOURS</div>
  <table class="abs hours" style="left:433px;top:1050px;border-collapse:collapse">
    <tr><td>Sunday &amp; Monday</td><td class="t">Closed</td></tr>
    <tr><td>Tuesday</td><td class="t">9:30AM – 5:00PM</td></tr>
    <tr><td>Wednesday</td><td class="t">Closed</td></tr>
    <tr><td>Thursday</td><td class="t">9:30AM – 5:00PM</td></tr>
    <tr><td>Friday</td><td class="t">9:00AM – 5:00PM</td></tr>
    <tr><td>Saturday</td><td class="t">9:00AM – 5:00PM</td></tr>
  </table>

  <div class="abs h3" style="left:593px;top:1031px;font-size:8.5px">CONTACT INFO</div>
  <svg class="ico" style="left:593px;top:1054px" width="9" height="12" viewBox="0 0 12 16"><path d="M6 0a6 6 0 0 0-6 6c0 4.5 6 10 6 10s6-5.5 6-10a6 6 0 0 0-6-6Zm0 8.5A2.5 2.5 0 1 1 6 3.5a2.5 2.5 0 0 1 0 5Z" fill="var(--teal)"/></svg>
  <div class="abs line" style="left:609px;top:1050px">2750 Harbor Lane, Suite 210,<br>Eastfield MA 02190</div>
  <svg class="ico" style="left:591px;top:1086px" width="10" height="10" viewBox="0 0 24 24"><path fill="var(--navy)" d="M6.6 10.8a15 15 0 0 0 6.6 6.6l2.2-2.2a1 1 0 0 1 1-.25 11.4 11.4 0 0 0 3.6.57 1 1 0 0 1 1 1V20a1 1 0 0 1-1 1A17 17 0 0 1 3 4a1 1 0 0 1 1-1h3.5a1 1 0 0 1 1 1c0 1.25.2 2.45.57 3.57a1 1 0 0 1-.25 1Z"/></svg>
  <div class="abs" style="left:609px;top:1085px;font-size:10px;font-weight:500;color:#444">555.214.7080</div>
  <svg class="ico" style="left:591px;top:1111px" width="11" height="8" viewBox="0 0 22 16"><rect width="22" height="16" rx="2" fill="var(--blue)"/><path d="M1 2l10 7 10-7" stroke="#fff" stroke-width="1.6" fill="none"/></svg>
  <div class="abs line" style="left:609px;top:1108px">info@thebrightarchclinic.com</div>
</footer>

<div class="abs bar"></div>
<div class="abs copy">© <span>The Bright Arch Clinic</span> – 2019. All Rights Reserved.</div>
<div class="abs credit">Eastfield Botox and Dermal Fillers</div>
</body>
</html>
```